Elevating our current Business Card Design

We want to elevate our current business card with a new design to look like a zenith 300 company. We are a premium lubricant distributor (oil and grease).
We need 2 versions, version 1 is as per the uploaded a copy of our current business card with the English version.
For our Chinese version we need to use the front to be English in English and have the back of the card designed exactly like the front for all info to be in Chinese.
The design template needs to be such that we can amend the template with adding different information for each person's card.
The background colour of the card can be changed- we just need to clearly see all information on the card and logos.
The QJR and Ember steady logos cannot have any colour or display changes- only use the logos attached.
All logos need to be included and all information from the attached current card

```html
<!DOCTYPE html>
<html lang="en">
<head>
<meta charset="utf-8">
<title>NORVA Business Cards</title>
<link rel="stylesheet" href="https://fonts.googleapis.com/css2?family=Montserrat:wght@400;500;700;800&family=Noto+Sans+SC:wght@400;500&display=swap">
<style>
  :root {
    --backdrop: #d6d6d6;
    --card: #ffffff;
    --brand-red: #d42a23;
    --deep-red: #b3201c;
    --rule: #a3231f;
    --ink: #444444;
    --gold: #f2ad1a;
    --badge-green: #2f4a36;
    --badge-orange: #ef7f1a;
    --badge-grey: #8c8c8c;
  }
  * { box-sizing: border-box; margin: 0; padding: 0; }
  html, body {
    width: 1200px; height: 896px; overflow: hidden;
    background: var(--backdrop);
  }
  .canvas { position: relative; width: 1200px; height: 896px; }
  .card {
    position: absolute; left: 335px; width: 525px; height: 300px;
    background: var(--card); border-radius: 26px;
    font-family: "Montserrat", "Noto Sans SC", sans-serif; color: var(--ink);
    box-shadow: 0 10px 24px rgba(0,0,0,0.18);
  }
  .card--english { top: 125px; }
  .card--chinese { top: 475px; font-family: "Montserrat", "Noto Sans SC", sans-serif; }
  .brand {
    position: absolute; right: 25px; top: 40px;
    display: flex; align-items: center; gap: 10px;
  }
  .brand__dot { width: 22px; height: 22px; border-radius: 50%; background: var(--gold); }
  .brand__name {
    font-weight: 800; font-size: 52px; letter-spacing: 1px;
    color: var(--brand-red); line-height: 1;
  }
  .tab {
    position: absolute; left: 0; top: 119px; width: 12px; height: 33px;
    background: var(--brand-red); border-radius: 0 10px 10px 0;
  }
  .person { position: absolute; left: 25px; top: 115px; }
  .person__name { font-weight: 700; font-size: 19px; color: var(--deep-red); line-height: 24px; letter-spacing: 0.2px; }
  .person__role { font-size: 14px; line-height: 20px; margin-top: -1px; }
  .card--chinese .person__name { font-family: "Noto Sans SC", sans-serif; font-weight: 500; font-size: 19px; }
  .card--chinese .person__role { font-family: "Noto Sans SC", sans-serif; }
  .rule { position: absolute; left: 25px; right: 25px; top: 168px; height: 1px; background: var(--rule); }
  .contacts { position: absolute; left: 25px; top: 181px; list-style: none; }
  .contacts li { display: flex; align-items: center; height: 19.4px; font-size: 13.5px; }
  .contacts svg { width: 12px; height: 12px; margin-right: 8px; fill: var(--brand-red); flex: none; }
  .address {
    position: absolute; right: 25px; top: 181px; text-align: right;
    font-size: 13.5px; line-height: 19.4px;
  }
  .card--chinese .address { font-family: "Montserrat", "Noto Sans SC", sans-serif; }
  .badges { position: absolute; right: 25px; top: 238px; display: flex; align-items: center; gap: 16px; }
  .badge--partner {
    width: 107px; height: 17px; background: var(--brand-red);
    transform: skewX(-8deg); border: 1px solid var(--brand-red);
    background: linear-gradient(90deg, #fff 0 50%, var(--brand-red) 50% 100%);
  }
  .badge--network { width: 46px; height: 32px; border-radius: 23px 23px 4px 4px; background: var(--badge-green); }
  .badge--cert { width: 38px; height: 38px; border-radius: 50%; background: var(--badge-orange); border: 4px solid var(--badge-grey); }
</style>
</head>
<body>
<main class="canvas">

  <section class="card card--english" aria-label="Business card, English side">
    <div class="brand"><span class="brand__dot"></span><span class="brand__name">NORVA</span></div>
    <span class="tab"></span>
    <div class="person">
      <p class="person__name">MARINA KOSTOV</p>
      <p class="person__role">Administration Executive</p>
    </div>
    <div class="rule"></div>
    <ul class="contacts">
      <li><svg viewBox="0 0 24 24"><path d="M6.6 10.8a15 15 0 0 0 6.6 6.6l2.2-2.2c.3-.3.7-.4 1-.2 1.1.4 2.3.6 3.6.6.6 0 1 .4 1 1V20c0 .6-.4 1-1 1A17 17 0 0 1 3 4c0-.6.4-1 1-1h3.5c.6 0 1 .4 1 1 0 1.3.2 2.5.6 3.6.1.3 0 .7-.2 1z"/></svg>1300 472 615</li>
      <li><svg viewBox="0 0 24 24"><path d="M7 1h10a2 2 0 0 1 2 2v18a2 2 0 0 1-2 2H7a2 2 0 0 1-2-2V3a2 2 0 0 1 2-2zm0 3v14h10V4zm5 15.5a1 1 0 1 0 0 2 1 1 0 0 0 0-2z"/></svg>+61 412 708 364</li>
      <li><svg viewBox="0 0 24 24"><path d="M6 2h12v5H6zM4 8h16a2 2 0 0 1 2 2v7h-4v5H6v-5H2v-7a2 2 0 0 1 2-2zm4 8v4h8v-4z"/></svg>+61 8 9274 5091</li>
      <li><svg viewBox="0 0 24 24"><path d="M2 5h20v14H2zm2 2v.5l8 5 8-5V7z"/></svg>marina.kostov@norvalube.com</li>
      <li><svg viewBox="0 0 24 24"><path d="M12 2a10 10 0 1 0 0 20 10 10 0 0 0 0-20zm-1 17.9A8 8 0 0 1 4.2 10L9 15v1a2 2 0 0 0 2 2zm6.9-2.5A2 2 0 0 0 16 16h-1v-3a1 1 0 0 0-1-1H8v-2h2a1 1 0 0 0 1-1V7h2a2 2 0 0 0 2-2v-.4a8 8 0 0 1 2.9 12.8z"/></svg>www.norvalube.com</li>
    </ul>
    <p class="address">48 Depot Parade<br>Harlow Vale, WA 6106</p>
    <div class="badges">
      <span class="badge--partner" role="img" aria-label="Talvor partner badge"></span>
      <span class="badge--network" role="img" aria-label="Ember steady network member badge"></span>
      <span class="badge--cert" role="img" aria-label="QJR certification badge"></span>
    </div>
  </section>

  <section class="card card--chinese" lang="zh" aria-label="Business card, Chinese side">
    <div class="brand"><span class="brand__dot"></span><span class="brand__name">NORVA</span></div>
    <span class="tab"></span>
    <div class="person">
      <p class="person__name">玛丽娜·科斯托夫</p>
      <p class="person__role">行政主管</p>
    </div>
    <div class="rule"></div>
    <ul class="contacts">
      <li><svg viewBox="0 0 24 24"><path d="M6.6 10.8a15 15 0 0 0 6.6 6.6l2.2-2.2c.3-.3.7-.4 1-.2 1.1.4 2.3.6 3.6.6.6 0 1 .4 1 1V20c0 .6-.4 1-1 1A17 17 0 0 1 3 4c0-.6.4-1 1-1h3.5c.6 0 1 .4 1 1 0 1.3.2 2.5.6 3.6.1.3 0 .7-.2 1z"/></svg>1300 472 615</li>
      <li><svg viewBox="0 0 24 24"><path d="M7 1h10a2 2 0 0 1 2 2v18a2 2 0 0 1-2 2H7a2 2 0 0 1-2-2V3a2 2 0 0 1 2-2zm0 3v14h10V4zm5 15.5a1 1 0 1 0 0 2 1 1 0 0 0 0-2z"/></svg>+61 412 708 364</li>
      <li><svg viewBox="0 0 24 24"><path d="M6 2h12v5H6zM4 8h16a2 2 0 0 1 2 2v7h-4v5H6v-5H2v-7a2 2 0 0 1 2-2zm4 8v4h8v-4z"/></svg>+61 8 9274 5091</li>
      <li><svg viewBox="0 0 24 24"><path d="M2 5h20v14H2zm2 2v.5l8 5 8-5V7z"/></svg>marina.kostov@norvalube.com</li>
      <li><svg viewBox="0 0 24 24"><path d="M12 2a10 10 0 1 0 0 20 10 10 0 0 0 0-20zm-1 17.9A8 8 0 0 1 4.2 10L9 15v1a2 2 0 0 0 2 2zm6.9-2.5A2 2 0 0 0 16 16h-1v-3a1 1 0 0 0-1-1H8v-2h2a1 1 0 0 0 1-1V7h2a2 2 0 0 0 2-2v-.4a8 8 0 0 1 2.9 12.8z"/></svg>www.norvalube.com</li>
    </ul>
    <p class="address">仓储大道48号<br>哈洛谷, 华盛顿州 6106</p>
    <div class="badges">
      <span class="badge--partner" role="img" aria-label="Talvor partner badge"></span>
      <span class="badge--network" role="img" aria-label="Ember steady network member badge"></span>
      <span class="badge--cert" role="img" aria-label="QJR certification badge"></span>
    </div>
  </section>

</main>
</body>
</html>
```